Walk Beside The River

Business Card design

Target Market(s)

People who require support in the commnity

Industry/Entity Type

Mental Health Support

Contact Information for Business Card

Mental Health Support Rosalind Tavener walkbesidetheriver@mailcove.com.au 0481 637 092 PO Box 926 Maroochydore QLD 4558

Colors
6B429C
8869AF
B7A5CE
E3DAEB
F3F0F8

Requirements
Must have
• Logo & details listed above
Should not have
• No red or orange

```html
<!DOCTYPE html>
<html lang="en">
<head>
<meta charset="utf-8">
<title>Walk Beside The River – Business Card</title>
<link rel="stylesheet" href="https://fonts.googleapis.com/css2?family=Open+Sans:wght@400;600;700;800&display=swap">
<style>
  :root {
    --stage: #222224;
    --card: #1f1e22;
    --yellow: #f0e82c;
    --purple: #6b429c;
    --cream: #f3f0f8;
    --white: #ffffff;
    --ink: #1f1e22;
  }
  * { box-sizing: border-box; margin: 0; padding: 0; }
  html, body { width: 1200px; height: 780px; overflow: hidden; background: var(--stage); }
  body {
    font-family: "Open Sans", Arial, sans-serif;
    display: flex; align-items: center; justify-content: center; gap: 40px;
  }
  .card {
    position: relative; width: 540px; height: 310px;
    border-radius: 22px; background: var(--card);
    box-shadow: 0 0 0 3px var(--yellow), 0 18px 30px rgba(0,0,0,.55);
    overflow: hidden;
  }
  .card-back__pattern {
    position: absolute; inset: 0;
    background:
      radial-gradient(ellipse at 85% 0%, rgba(255,255,255,.28), rgba(255,255,255,0) 55%),
      linear-gradient(160deg, #2a292e 0%, #1c1b1f 60%, #18171a 100%);
  }
  .name-block {
    position: absolute; left: 0; top: 118px;
    display: flex; align-items: stretch;
  }
  .name-block__bar { width: 26px; background: var(--yellow); }
  .name-block__text { padding-left: 10px; }
  .person-name { font-weight: 800; font-size: 26px; line-height: 1.05; color: var(--yellow); }
  .person-name__surname { color: var(--purple); }
  .person-title { font-size: 13px; font-weight: 600; color: var(--white); margin-top: 3px; }
  .brand {
    position: absolute; right: 26px; top: 26px;
    display: flex; align-items: center; gap: 14px;
  }
  .brand__name {
    font-weight: 700; font-size: 15px; line-height: 1.25;
    color: var(--cream); text-align: right; letter-spacing: .04em;
    text-transform: uppercase;
  }
  .brand__dot { width: 100px; height: 100px; border-radius: 50%; background: var(--purple); }
  .contacts {
    position: absolute; left: 96px; top: 178px;
    list-style: none; display: grid; gap: 4px;
  }
  .contacts__item {
    display: flex; align-items: center; gap: 9px;
    font-size: 13px; color: var(--white);
  }
  .contacts__icon { width: 14px; height: 14px; flex: none; }
  .tagline-band {
    position: absolute; left: 0; right: 0; top: 256px; height: 30px;
    background: var(--yellow);
    display: flex; align-items: center; justify-content: flex-end;
    padding-right: 70px;
    font-size: 13px; font-weight: 600; color: var(--ink);
  }
</style>
</head>
<body>

  <section class="card card-back">
    <div class="card-back__pattern" role="img" aria-label="Repeating star pattern with a large yellow star mark at the centre"></div>
  </section>

  <section class="card card-front">
    <div class="brand">
      <p class="brand__name">Walk Beside<br>The River</p>
      <span class="brand__dot"></span>
    </div>

    <div class="name-block">
      <span class="name-block__bar"></span>
      <div class="name-block__text">
        <h1 class="person-name">Maja <span class="person-name__surname">Kovarik</span></h1>
        <p class="person-title">CEO/Director</p>
      </div>
    </div>

    <ul class="contacts">
      <li class="contacts__item">
        <svg class="contacts__icon" viewBox="0 0 24 24" fill="#f0e82c"><path d="M6.6 10.8a15 15 0 0 0 6.6 6.6l2.2-2.2c.3-.3.7-.4 1-.2 1.1.4 2.3.6 3.6.6.6 0 1 .4 1 1V20c0 .6-.4 1-1 1A17 17 0 0 1 3 4c0-.6.4-1 1-1h3.5c.6 0 1 .4 1 1 0 1.3.2 2.5.6 3.6.1.3 0 .7-.2 1z"/></svg>
        0481 637 092
      </li>
      <li class="contacts__item">
        <svg class="contacts__icon" viewBox="0 0 24 24" fill="none" stroke="#f0e82c" stroke-width="2"><rect x="3" y="5" width="18" height="14" rx="2"/><path d="M3 7l9 6 9-6"/></svg>
        walkbesidetheriver@mailcove.com.au
      </li>
      <li class="contacts__item">
        <svg class="contacts__icon" viewBox="0 0 24 24" fill="none" stroke="#f0e82c" stroke-width="2"><path d="M12 22s7-7 7-12a7 7 0 0 0-14 0c0 5 7 12 7 12z"/><circle cx="12" cy="10" r="2.5"/></svg>
        PO Box 926 Maroochydore QLD 4558
      </li>
    </ul>

    <p class="tagline-band">Mental Health Support Rosalind Tavener</p>
  </section>

</body>
</html>
```